Specialised investor in e-mobility and energy wants business card design

We need a business card design that fits our existing corporate design. <The look and feel must be 'sharp'/'clean', dynamic, communicate momentum, professionalism etc (as one would imagine from a firm in the financial sector). We like the idea of a reverse-side of the card that includes the logo, and the name and contact details on the other. We expect the deliverable to be whatever format might be required to be able to get cards printed directly by a service such as kelmo press. Our website is www.zub.capital

```html
<!DOCTYPE html>
<html lang="en">
<head>
<meta charset="utf-8">
<title>ZUB Capital – Business Card</title>
<link href="https://fonts.googleapis.com/css2?family=Questrial&family=Montserrat:wght@400;600&display=swap" rel="stylesheet">
<style>
  :root {
    --bg: #3a3b3d;
    --white: #ffffff;
    --green-dark: #145a1c;
    --green-deep: #0f4716;
    --green-light: #6db33f;
    --ink: #2b2b2b;
    --rule: #9a9a9a;
  }
  * { margin: 0; padding: 0; box-sizing: border-box; }
  html, body { width: 1200px; height: 1200px; overflow: hidden; }
  body {
    background: var(--bg);
    position: relative;
    font-family: "Questrial", "Century Gothic", sans-serif;
  }
  .card {
    position: absolute;
    left: 150px;
    width: 900px;
    height: 514px;
    border-radius: 40px;
    overflow: hidden;
  }
  /* Front side */
  .card-front { top: 58px; background: var(--white); }
  .card-front .brand {
    position: absolute; left: 210px; top: 112px;
    font-size: 76px; color: var(--green-dark); letter-spacing: 1px;
  }
  .identity {
    position: absolute; left: 100px; top: 328px;
    padding-left: 16px; border-left: 6px solid var(--green-light);
    font-family: "Montserrat", Arial, sans-serif;
    line-height: 1.05;
  }
  .identity .full-name { font-weight: 600; font-size: 30px; color: var(--green-light); letter-spacing: -0.5px; }
  .identity .position { font-weight: 400; font-size: 24px; color: var(--ink); }
  .divider {
    position: absolute; left: 568px; top: 262px;
    width: 1px; height: 150px; background: var(--rule);
  }
  .contact {
    position: absolute; left: 604px; top: 258px;
    list-style: none; font-family: "Montserrat", Arial, sans-serif;
    font-size: 21px; color: var(--ink);
  }
  .contact li { display: flex; align-items: center; gap: 12px; height: 40px; }
  .contact svg { width: 24px; height: 24px; flex: none; }
  .band-dark {
    position: absolute; left: 0; bottom: 0;
    width: 560px; height: 26px; background: var(--green-dark);
  }
  .band-light {
    position: absolute; right: 0; bottom: 0;
    width: 332px; height: 44px; background: var(--green-light);
  }
  /* Back side */
  .card-back {
    top: 628px;
    background: linear-gradient(100deg, var(--green-deep) 0%, var(--green-dark) 45%, #1d5e27 55%, var(--green-deep) 100%);
    display: flex; align-items: center; justify-content: center;
  }
  .card-back .brand { font-size: 92px; color: var(--white); letter-spacing: 1px; }
</style>
</head>
<body>
  <section class="card card-front" aria-label="Card front">
    <div class="brand">ZUB Capital</div>
    <div class="identity">
      <div class="full-name">FULL NAME</div>
      <div class="position">POSITION</div>
    </div>
    <div class="divider"></div>
    <ul class="contact">
      <li>
        <svg viewBox="0 0 24 24" aria-hidden="true"><path fill="#6db33f" d="M6.6 10.8a15 15 0 0 0 6.6 6.6l2.2-2.2c.3-.3.7-.4 1-.2 1.1.4 2.3.6 3.6.6.6 0 1 .4 1 1V20c0 .6-.4 1-1 1A17 17 0 0 1 3 4c0-.6.4-1 1-1h3.5c.6 0 1 .4 1 1 0 1.3.2 2.5.6 3.6.1.3 0 .7-.2 1z"/></svg>
        +41 70555 0148
      </li>
      <li>
        <svg viewBox="0 0 24 24" aria-hidden="true"><rect x="2" y="5" width="20" height="14" fill="#6db33f"/><path d="M2 5l10 8 10-8" fill="none" stroke="#fff" stroke-width="1.6"/></svg>
        mara@zub.capital
      </li>
      <li>
        <svg viewBox="0 0 24 24" aria-hidden="true"><g fill="none" stroke="#6db33f" stroke-width="1.6"><circle cx="12" cy="12" r="9.5"/><ellipse cx="12" cy="12" rx="4" ry="9.5"/><path d="M2.5 12h19M4 7h16M4 17h16"/></g></svg>
        www.zub.capital
      </li>
    </ul>
    <div class="band-dark"></div>
    <div class="band-light"></div>
  </section>

  <section class="card card-back" aria-label="Card back">
    <div class="brand">ZUB Capital</div>
  </section>
</body>
</html>
```